New Business Card Design Project

I'd like a business card design around the same modern style that I used on my website www.brovanhs.com
It's gonna be one of those round corners double-sided business cards with maybe a big logo on the front and all the info on the back of the card.

Contact Information for Business Card

Marco Delgado
425-317-6084
www.brovanhs.com

www.facebook.com/BrovanHomeServices
www.intsgram.com/BrovanHomeServices

Requirements
Must have
• it needs to look elegant and modern

```html
<!DOCTYPE html>
<html lang="en">
<head>
<meta charset="utf-8">
<title>Brovan Home Services – Business Card</title>
<link rel="stylesheet" href="https://fonts.googleapis.com/css2?family=Open+Sans:wght@700&family=Montserrat:wght@400;500;600&display=swap">
<style>
  :root {
    --page-bg: #e9e6e2;
    --card-light: #f3f4f5;
    --card-mid: #dfe4e9;
    --brand-blue: #1b6fc8;
    --band-dark: #232123;
    --band-edge: #3a3638;
    --accent-line: #d9c7c4;
    --text-light: #e4dcd9;
    --icon-teal: #2a8fc2;
  }
  * { margin: 0; padding: 0; box-sizing: border-box; }
  html, body {
    width: 1200px; height: 970px; overflow: hidden;
    background: var(--page-bg);
  }
  .card {
    position: absolute; left: 80px; top: 188px;
    width: 1040px; height: 594px;
    border-radius: 18px; overflow: hidden;
    background: linear-gradient(135deg, var(--card-light) 0%, var(--card-mid) 55%, var(--card-light) 100%);
    box-shadow: 0 10px 30px rgba(0,0,0,0.18);
  }
  .brand {
    position: absolute; left: 480px; top: 100px; width: 500px;
    text-align: center; color: var(--brand-blue);
    font-family: "Open Sans", Arial, sans-serif; font-weight: 700;
    line-height: 1;
  }
  .brand-name { font-size: 104px; letter-spacing: -1px; }
  .brand-tagline { font-size: 27px; letter-spacing: 1px; margin-top: 14px; text-transform: uppercase; }
  .info-band {
    position: absolute; left: 0; bottom: 0; width: 100%; height: 165px;
    background: linear-gradient(180deg, var(--band-edge), var(--band-dark));
  }
  .info-band::before {
    content: ""; position: absolute; left: 0; top: -34px; width: 100%; height: 6px;
    background: var(--accent-line);
  }
  .info-band::after {
    content: ""; position: absolute; left: 0; top: -28px; width: 100%; height: 28px;
    background: var(--band-dark);
  }
  .person-name {
    position: absolute; left: 110px; top: 438px;
    font-family: "Montserrat", Arial, sans-serif; font-weight: 600;
    font-size: 30px; color: var(--text-light); z-index: 2;
  }
  .contact-list {
    position: absolute; top: 500px; list-style: none;
    font-family: "Montserrat", Arial, sans-serif; font-weight: 400;
    font-size: 25px; color: var(--text-light); letter-spacing: 0.5px;
  }
  .contact-list li { display: flex; align-items: center; gap: 12px; height: 32px; }
  .contact-left { left: 60px; }
  .contact-right { left: 605px; }
  .icon { width: 26px; height: 26px; flex: none; }
</style>
</head>
<body>
  <div class="card">
    <div class="brand">
      <div class="brand-name">Brovan</div>
      <div class="brand-tagline">Home Services</div>
    </div>

    <div class="info-band"></div>
    <div class="person-name">Marco Delgado</div>

    <ul class="contact-list contact-left">
      <li>
        <svg class="icon" viewBox="0 0 26 26" aria-hidden="true">
          <rect width="26" height="26" rx="3" fill="var(--icon-teal)"/>
          <path d="M8 6c1-1 2-1 3 0l1.5 2.5c.5 1 0 1.8-.7 2.3l-.8.6c.8 1.8 2 3 3.8 3.8l.6-.8c.5-.7 1.3-1.2 2.3-.7L20 15c1 1 1 2 0 3-2 2-5 1.5-8-1.5S6 8 8 6z" fill="#1d1b1c"/>
        </svg>
        <span>425-317-6084</span>
      </li>
      <li>
        <svg class="icon" viewBox="0 0 26 26" aria-hidden="true">
          <circle cx="13" cy="13" r="12" fill="var(--icon-teal)"/>
          <g fill="none" stroke="#1d1b1c" stroke-width="1.5">
            <circle cx="13" cy="13" r="8"/>
            <ellipse cx="13" cy="13" rx="3.5" ry="8"/>
            <path d="M5 13h16M6.5 9h13M6.5 17h13"/>
          </g>
        </svg>
        <span>www.brovanhs.com</span>
      </li>
    </ul>

    <ul class="contact-list contact-right">
      <li>
        <svg class="icon" viewBox="0 0 26 26" aria-hidden="true"><rect width="26" height="26" rx="3" fill="var(--icon-teal)"/></svg>
        <span>BrovanHomeServices</span>
      </li>
      <li>
        <svg class="icon" viewBox="0 0 26 26" aria-hidden="true"><rect width="26" height="26" rx="3" fill="var(--icon-teal)"/></svg>
        <span>BrovanHomeServices</span>
      </li>
    </ul>
  </div>
</body>
</html>
```